Orvane Group Business Card

Building Management company based in Sydney, Australia. We provide onsite management for commercial and residential buildings.
I would like a sophisticated minimalist design that indicates that we provide a high-end service. I would like a silver or metal look background or something similar.
The business card should have:
Name
Title
email
Office Phone
Mobile
Address
Website
The services that we provide should be prominent:
Building Management - Concierge - Caretaking - Cleaning

```html
<!DOCTYPE html>
<html lang="en">
<head>
<meta charset="utf-8">
<title>Orvane Group Business Card</title>
<link rel="stylesheet" href="https://fonts.googleapis.com/css2?family=Source+Sans+3:wght@400;600;700&display=swap">
<style>
  :root {
    --brand-blue: #1f5fa3;
    --ink-black: #0d0d0d;
    --card-white: #ffffff;
    --silver-light: #f4f5f7;
    --silver-mid: #dfe2e6;
    --text-grey: #3a3a3a;
    --page-bg: #e7e8ea;
  }
  html, body {
    margin: 0;
    padding: 0;
    width: 1200px;
    height: 1200px;
    overflow: hidden;
    background: var(--page-bg);
    font-family: "Source Sans 3", sans-serif;
  }
  .sheet {
    width: 1200px;
    height: 1200px;
    display: flex;
    flex-direction: column;
    align-items: center;
    justify-content: center;
    gap: 60px;
  }
  .card {
    position: relative;
    width: 840px;
    height: 480px;
    box-shadow: 0 6px 18px rgba(0,0,0,0.18);
    overflow: hidden;
  }
  .card-back {
    background: var(--brand-blue);
    display: flex;
    flex-direction: column;
    align-items: center;
    justify-content: center;
    gap: 22px;
  }
  .back-name {
    color: var(--card-white);
    font-weight: 700;
    font-size: 44px;
    letter-spacing: 2px;
    text-transform: uppercase;
  }
  .service-list {
    margin: 0;
    padding: 0;
    list-style: none;
    display: flex;
    gap: 14px;
    color: var(--card-white);
    font-size: 21px;
    font-weight: 600;
    letter-spacing: 1px;
  }
  .service-list li + li::before {
    content: "·";
    margin-right: 14px;
  }
  .card-front {
    background: linear-gradient(135deg, var(--card-white) 0%, var(--silver-light) 45%, var(--silver-mid) 100%);
  }
  .front-shapes {
    position: absolute;
    inset: 0;
  }
  .holder {
    position: absolute;
    left: 92px;
    top: 28px;
  }
  .holder-name {
    margin: 0;
    color: var(--brand-blue);
    font-weight: 700;
    font-size: 30px;
    line-height: 1.1;
  }
  .holder-title {
    margin: 2px 0 0;
    color: var(--text-grey);
    font-size: 19px;
  }
  .contact {
    position: absolute;
    left: 40px;
    top: 172px;
    margin: 0;
    color: var(--text-grey);
    font-size: 19px;
    line-height: 1.3;
    font-style: normal;
  }
  .contact .label {
    color: var(--brand-blue);
    font-weight: 600;
  }
  .brand-mark {
    position: absolute;
    right: 70px;
    top: 190px;
    display: flex;
    align-items: center;
    gap: 12px;
  }
  .brand-square {
    width: 26px;
    height: 26px;
    background: var(--brand-blue);
  }
  .brand-name {
    color: var(--ink-black);
    font-weight: 700;
    font-size: 40px;
    letter-spacing: 1px;
    text-transform: uppercase;
  }
</style>
</head>
<body>
  <main class="sheet">
    <section class="card card-back" aria-label="Card back">
      <span class="back-name">Orvane Group</span>
      <ul class="service-list">
        <li>Building Management</li>
        <li>Concierge</li>
        <li>Caretaking</li>
        <li>Cleaning</li>
      </ul>
    </section>

    <section class="card card-front" aria-label="Card front">
      <svg class="front-shapes" width="840" height="480" viewBox="0 0 840 480" aria-hidden="true">
        <polygon points="22,28 58,28 36,64 22,64" fill="var(--brand-blue)"/>
        <polygon points="64,28 82,28 82,64 42,64" fill="var(--ink-black)"/>
        <polygon points="0,392 330,392 318,412 0,412" fill="var(--brand-blue)"/>
        <polygon points="346,392 840,392 840,480 296,480" fill="var(--ink-black)"/>
      </svg>

      <div class="holder">
        <h1 class="holder-name">Dane Whitlow</h1>
        <p class="holder-title">Managing Director</p>
      </div>

      <address class="contact">
        12345, Address Goes Here<br>
        Sydney NSW, 2000<br>
        <span class="label">p:</span> 044-555 210 384<br>
        <span class="label">m:</span> 0412 555 093<br>
        <span class="label">e:</span> info@orvanegroup.com<br>
        <span class="label">w:</span> orvanegroup.com.au
      </address>

      <div class="brand-mark">
        <span class="brand-square"></span>
        <span class="brand-name">Orvane Group</span>
      </div>
    </section>
  </main>
</body>
</html>
```